MRT Property - Business Cards

Looking for a business card & general letterhead, signage etc design for our new logo.

Colours:
000a20
0056a2
00b5ef
0088ce
68cef2

Fonts:
Poppins
Karla

Please keep look and feel of new brand - example in the zip package I sent.

```html
<!DOCTYPE html>
<html lang="en">
<head>
<meta charset="UTF-8">
<title>MRT Property – Business Cards</title>
<link href="https://fonts.googleapis.com/css2?family=Poppins:wght@400;500;600;700&family=Karla:wght@400;500&display=swap" rel="stylesheet">
<style>
  :root {
    --ink-navy: #000a20;
    --brand-blue: #0056a2;
    --brand-cyan: #00b5ef;
    --brand-mid: #0088ce;
    --brand-light: #68cef2;
    --card-white: #ffffff;
    --text-dark: #1a1a1a;
    --stage: #e9ebef;
  }
  * { box-sizing: border-box; margin: 0; padding: 0; }
  html, body {
    width: 1200px; height: 880px; overflow: hidden;
    background: var(--stage);
    font-family: "Karla", sans-serif;
  }
  .sheet {
    position: relative; width: 1200px; height: 880px;
    display: flex; flex-direction: column; align-items: center; justify-content: center; gap: 44px;
  }
  .card {
    position: relative; width: 630px; height: 360px;
    border-radius: 26px; overflow: hidden;
    box-shadow: 0 10px 30px rgba(0, 10, 32, 0.18);
  }
  .card-back { background: #0b0b0c; }
  .card-back .pattern-area {
    position: absolute; inset: 0;
    background: linear-gradient(160deg, #3a3a3c 0%, #111112 40%, #050505 100%);
  }
  .card-front { background: var(--card-white); }
  .brand-lockup {
    position: absolute; left: 44px; top: 158px;
    display: flex; align-items: center; gap: 12px;
    white-space: nowrap;
  }
  .brand-dot {
    width: 30px; height: 30px; border-radius: 50%;
    background: var(--brand-mid); flex: none;
  }
  .brand-name {
    font-family: "Poppins", sans-serif; font-weight: 700;
    font-size: 28px; line-height: 1; color: var(--brand-blue); letter-spacing: 0.3px;
  }
  .divider {
    position: absolute; left: 350px; top: 70px;
    width: 1.5px; height: 218px; background: var(--brand-cyan);
  }
  .details {
    position: absolute; left: 376px; top: 70px;
    color: var(--text-dark);
  }
  .person-name {
    font-family: "Poppins", sans-serif; font-weight: 600;
    font-size: 25px; color: var(--brand-blue); letter-spacing: 1px; line-height: 1.1;
  }
  .person-role { font-size: 17px; margin-top: 2px; }
  .contact-list { list-style: none; margin-top: 16px; }
  .contact-list li {
    display: flex; align-items: center; gap: 10px;
    font-size: 17px; line-height: 27px; white-space: nowrap;
  }
  .contact-list svg { width: 16px; height: 16px; flex: none; }
  .address { font-size: 17px; line-height: 24px; margin-top: 14px; padding-left: 26px; }
</style>
</head>
<body>
<main class="sheet">
  <section class="card card-back">
    <div class="pattern-area" role="img" aria-label="Glossy black card back with repeating brand-symbol pattern"></div>
  </section>

  <section class="card card-front">
    <div class="brand-lockup">
      <span class="brand-dot"></span>
      <span class="brand-name">MRT Property</span>
    </div>
    <div class="divider"></div>
    <div class="details">
      <h1 class="person-name">DANIEL REED</h1>
      <p class="person-role">Managing Director</p>
      <ul class="contact-list">
        <li>
          <svg viewBox="0 0 16 16" aria-hidden="true"><circle cx="8" cy="8" r="8" fill="var(--brand-blue)"/><path d="M5 4.5c.5-.4 1-.4 1.3.1l.7 1.2c.2.4.1.7-.2 1l-.4.3c.4.9 1 1.5 1.9 1.9l.3-.4c.3-.3.6-.4 1-.2l1.2.7c.5.3.5.8.1 1.3-.6.7-1.5.9-2.4.4C6.8 10 6 9.2 5.2 7.6c-.5-1-.3-2.4-.2-3.1z" fill="#fff"/></svg>
          123 456 789
        </li>
        <li>
          <svg viewBox="0 0 16 16" aria-hidden="true"><rect x="1" y="3" width="14" height="10" rx="1.5" fill="var(--brand-blue)"/><path d="M2 4l6 5 6-5" stroke="#fff" stroke-width="1.2" fill="none"/></svg>
          info@yourgmail.com
        </li>
        <li>
          <svg viewBox="0 0 16 16" aria-hidden="true"><circle cx="8" cy="8" r="7.5" fill="var(--brand-blue)"/><ellipse cx="8" cy="8" rx="3" ry="7" stroke="#fff" fill="none"/><path d="M1 8h14" stroke="#fff"/></svg>
          www.yourwebsite.com
        </li>
      </ul>
      <p class="address">Your address, City<br>State, Zip 1234</p>
    </div>
  </section>
</main>
</body>
</html>
```